Business Cards for new orthopaedic surgery practice

My husband and I are starting our own orthopaedic surgery practice. We are looking for a business card that is uniform, but one will have my name/title and the other will have his. You can just create one design with my name on it for now. But when I choose your design as the winning design I will ask that you add another copy with his name/title.

We are looking for classy, simple, elite all in one. We like dark blues/a little gold/yellow. Something that goes with our logo. We want our logo incorporated. Here is all the info you need:
Business name: RV Bone & Vitality Center
Location: 38517 North Willowmere Ave
Fernbrook Glen, FL 32960
Phone: 954-218-4063
Fax: 954-582-7341
Email: info@myrvbonecare.example

Names: Lydia Vance, M.D.
Board Certified Hand and Upper Extremity Surgeon

Ebo Dansu, M.D.
Board Certified Hip & Knee Replacement/General Orthopaedic Surgeon

Can decide what you want to put on the back. Maybe a slogan:
Rooted in Care. Focused on You

I am just going to upload our logo. The only thing is if we select you as the winning design, the location, and phone numbers may change. We will need your help to update that once fully solidified.

Industry/Entity Type

Medical

Contact Information for Business Card

Colors
0054AA
0677BA
7BADD7
CADEEF
E8F1F8
0094D4
00A9DD
6FCCEA
C7EBF8
E9F6FB

Requirements
Must have
• class, appeal,
Should not have
• We want to air on the side of masculine if we are looking at masculine vs. feminine feel. But we still want it classy, sophisticated, and something we will love

```html
<!DOCTYPE html>
<html lang="en">
<head>
<meta charset="utf-8">
<title>RV Bone &amp; Vitality Center – Business Card</title>
<link href="https://fonts.googleapis.com/css2?family=Arimo:wght@400&family=Playfair+Display:wght@600;700&display=swap" rel="stylesheet">
<style>
  :root {
    --page: #05062a;
    --navy-deep: #0c0b2e;
    --navy: #25225f;
    --navy-mid: #1d1a52;
    --brand-blue: #1f3c8f;
    --emboss: #2a3f96;
    --cyan: #1ab2e2;
    --white: #ffffff;
    --serif: "Playfair Display", Georgia, serif;
    --sans: "Arimo", Arial, sans-serif;
  }
  * { margin: 0; padding: 0; box-sizing: border-box; }
  html, body { width: 1200px; height: 801px; overflow: hidden; }
  body {
    background: var(--page);
    display: flex;
    flex-direction: column;
    align-items: center;
    justify-content: center;
    gap: 36px;
  }
  .card {
    position: relative;
    width: 620px;
    height: 354px;
    overflow: hidden;
  }

  /* Back side */
  .card--back {
    background: linear-gradient(160deg, var(--navy) 0%, var(--navy-mid) 45%, var(--navy-deep) 100%);
    display: flex;
    align-items: center;
    justify-content: center;
  }
  .back-brand {
    font-family: var(--serif);
    font-weight: 600;
    font-size: 34px;
    letter-spacing: 1px;
    color: var(--emboss);
  }

  /* Front side */
  .card--front {
    border: 3px solid var(--cyan);
    background:
      linear-gradient(200deg, var(--white) 0%, #f2f2f6 22%, #8c89a6 38%, var(--navy-deep) 55%, var(--navy) 78%, var(--navy-mid) 100%);
  }
  .front-brand {
    position: absolute;
    top: 40px;
    right: 36px;
    display: flex;
    align-items: center;
    gap: 10px;
  }
  .front-brand__mark {
    width: 12px;
    height: 12px;
    background: var(--brand-blue);
  }
  .front-brand__name {
    font-family: var(--serif);
    font-weight: 600;
    font-size: 19px;
    color: var(--brand-blue);
  }
  .person {
    position: absolute;
    top: 110px;
    left: 0;
    padding-left: 34px;
  }
  .person__marker {
    position: absolute;
    left: 12px;
    top: 8px;
    width: 12px;
    height: 18px;
    background: var(--cyan);
  }
  .person__name {
    font-family: var(--serif);
    font-weight: 700;
    font-size: 26px;
    color: var(--cyan);
    line-height: 1.2;
  }
  .person__title {
    font-family: var(--sans);
    font-size: 15px;
    color: var(--white);
    line-height: 1.35;
    margin-top: 6px;
  }
  .contact {
    position: absolute;
    left: 56px;
    bottom: 34px;
    list-style: none;
  }
  .contact__item {
    display: flex;
    align-items: center;
    gap: 12px;
    font-family: var(--sans);
    font-size: 15px;
    color: var(--white);
    line-height: 1.6;
  }
  .contact__icon { width: 15px; height: 15px; flex: none; }
  .address {
    position: absolute;
    right: 40px;
    bottom: 80px;
    display: flex;
    align-items: center;
    gap: 16px;
  }
  .address__rule {
    display: flex;
    gap: 5px;
    height: 52px;
  }
  .address__rule span {
    width: 2px;
    height: 100%;
    background: var(--cyan);
  }
  .address__text {
    font-family: var(--sans);
    font-size: 15px;
    color: var(--white);
    line-height: 1.45;
  }
</style>
</head>
<body>

  <section class="card card--back" aria-label="Card back">
    <p class="back-brand">RV Bone &amp; Vitality Center</p>
  </section>

  <section class="card card--front" aria-label="Card front">
    <div class="front-brand">
      <span class="front-brand__mark"></span>
      <span class="front-brand__name">RV Bone &amp; Vitality Center</span>
    </div>

    <div class="person">
      <span class="person__marker"></span>
      <h1 class="person__name">Lydia Vance, M.D.</h1>
      <p class="person__title">Board Certified Hand and<br>Upper Extremity Surgeon</p>
    </div>

    <ul class="contact">
      <li class="contact__item">
        <svg class="contact__icon" viewBox="0 0 16 16" aria-hidden="true">
          <rect x="4" y="1" width="8" height="14" rx="1.5" fill="none" stroke="#1ab2e2" stroke-width="1.6"/>
          <line x1="7" y1="12.5" x2="9" y2="12.5" stroke="#1ab2e2" stroke-width="1.4"/>
        </svg>
        954-218-4063
      </li>
      <li class="contact__item">
        <svg class="contact__icon" viewBox="0 0 16 16" aria-hidden="true">
          <rect x="4" y="1" width="8" height="4" fill="none" stroke="#1ab2e2" stroke-width="1.4"/>
          <rect x="1.5" y="5" width="13" height="6" rx="1" fill="#1ab2e2"/>
          <rect x="4" y="9" width="8" height="6" fill="#0c0b2e" stroke="#1ab2e2" stroke-width="1.4"/>
        </svg>
        954-582-7341
      </li>
      <li class="contact__item">
        <svg class="contact__icon" viewBox="0 0 16 16" aria-hidden="true">
          <path d="M1 8 L15 1 L11 15 L8 10 Z" fill="#1ab2e2"/>
          <path d="M8 10 L15 1" stroke="#0c0b2e" stroke-width="1"/>
        </svg>
        info@myrvbonecare.example
      </li>
    </ul>

    <div class="address">
      <div class="address__rule"><span></span><span></span></div>
      <p class="address__text">38517 North Willowmere Ave<br>Fernbrook Glen, FL 32960</p>
    </div>
  </section>

</body>
</html>
```